Boutique custom software development company needs new business card

Our nearly 20 year old custom software development company would like to better include the fact that we are now providing Bitcoin services. These new services are B2B include education (how to acquire and securely hold Bitcoin) and integrating Bitcoin payments into existing ecommerce sites or other existing systems. Please keep the card clean and simple. Attached is our current design and some other files. vextorial.com

Target Market(s)

businesses owners interested in long term relationship

Industry/Entity Type

Custom software development and Bitcoin

Contact Information for Business Card

Dale Parker, dale@vextorial.com, vextorial.com, (888) 555-VXTRL

Font styles to use
Other font styles liked:
• monospace

Requirements
Must have
• double-sided
Nice to have
• clean and simple
Should not have
• physical address

```html
<!DOCTYPE html>
<html lang="en">
<head>
<meta charset="utf-8">
<title>Vextorial business card</title>
<link rel="stylesheet" href="https://fonts.googleapis.com/css2?family=Roboto+Mono:wght@400;500;700&family=Montserrat:wght@300&family=Oswald:wght@500&display=swap">
<style>
  :root {
    --stage: #18181b;
    --card: #2b3587;
    --card-deep: #252e7a;
    --accent: #f47b20;
    --ink: #ffffff;
    --ink-soft: #d9dcf0;
  }
  * { box-sizing: border-box; margin: 0; padding: 0; }
  html, body {
    width: 1200px; height: 936px; overflow: hidden;
    background: var(--stage);
  }
  .sheet {
    position: relative; width: 1200px; height: 936px;
    display: flex; flex-direction: column; align-items: center;
    justify-content: center; gap: 40px;
  }
  .card {
    position: relative; width: 700px; height: 400px;
    border-radius: 28px; background: var(--card); overflow: hidden;
    color: var(--ink);
  }
  .wordmark {
    display: flex; align-items: center; gap: 12px;
    font-family: "Roboto Mono", monospace; font-weight: 700;
    color: var(--ink); letter-spacing: 1px; line-height: 1.1;
  }
  .wordmark-square { background: var(--accent); flex: none; }
  .tagline {
    font-family: "Montserrat", sans-serif; font-weight: 300;
    color: var(--ink);
  }

  /* Front */
  .front .brand { position: absolute; left: 48px; top: 60px; }
  .front .wordmark { font-size: 44px; }
  .front .wordmark-square { width: 22px; height: 22px; }
  .front .tagline { font-size: 17px; margin-top: 4px; margin-left: 34px; }
  .front .holder {
    position: absolute; right: 48px; top: 172px;
    font-family: "Oswald", sans-serif; font-weight: 500;
    font-size: 30px; letter-spacing: 3px; color: var(--accent);
    text-transform: uppercase;
  }
  .front .rule {
    position: absolute; left: 48px; right: 24px; top: 226px;
    height: 1px; background: var(--accent);
  }
  .contact-list {
    position: absolute; left: 48px; top: 252px; list-style: none;
    font-family: "Roboto Mono", monospace; font-size: 17px;
    line-height: 30px; color: var(--ink);
  }
  .contact-list li { display: flex; align-items: center; gap: 12px; }
  .contact-list svg { width: 15px; height: 15px; flex: none; }

  /* Back */
  .back {
    background: radial-gradient(ellipse at 60% 40%, var(--card) 0%, var(--card-deep) 100%);
  }
  .back .brand { position: absolute; left: 130px; top: 34px; }
  .back .wordmark { font-size: 54px; }
  .back .wordmark-square { width: 26px; height: 26px; }
  .back .tagline { font-size: 21px; margin-top: 2px; margin-left: 38px; }
  .services { position: absolute; left: 168px; top: 158px; }
  .services-title {
    font-family: "Roboto Mono", monospace; font-weight: 500;
    font-size: 16px; color: var(--accent); letter-spacing: 1px;
    margin-bottom: 5px; text-transform: uppercase;
  }
  .services-list {
    list-style: none; font-family: "Roboto Mono", monospace;
    font-size: 14.5px; line-height: 23px; color: var(--ink-soft);
  }
  .services-list li { position: relative; padding-left: 18px; }
  .services-list li::before {
    content: "•"; position: absolute; left: 0; color: var(--accent);
  }
  .services-list .service-bitcoin { color: var(--ink); font-weight: 500; }
</style>
</head>
<body>
<main class="sheet">
  <section class="card front" aria-label="Card front">
    <div class="brand">
      <div class="wordmark"><span class="wordmark-square"></span>VEXTORIAL</div>
      <div class="tagline">developer of custom applications</div>
    </div>
    <h1 class="holder">Dale Parker</h1>
    <div class="rule"></div>
    <ul class="contact-list">
      <li>
        <svg viewBox="0 0 16 16" aria-hidden="true"><path fill="#f47b20" d="M3.5 1.5l2.5 2.8-1.4 1.9c.9 1.9 2.4 3.4 4.3 4.3l1.9-1.4 2.8 2.5-1.3 2.2C7.2 13.4 2.6 8.8 1.2 3.7z"/></svg>
        (888) 555-VXTRL
      </li>
      <li>
        <svg viewBox="0 0 16 16" aria-hidden="true"><rect x="1" y="3.5" width="14" height="9" fill="#f47b20"/><path d="M1.5 4l6.5 5 6.5-5" fill="none" stroke="#2b3587" stroke-width="1.3"/></svg>
        dale@vextorial.com
      </li>
      <li>
        <svg viewBox="0 0 16 16" aria-hidden="true"><circle cx="8" cy="8" r="7" fill="#f47b20"/><path d="M1 8h14M8 1c-3 3.5-3 10.5 0 14M8 1c3 3.5 3 10.5 0 14" fill="none" stroke="#2b3587" stroke-width="1"/></svg>
        vextorial.com
      </li>
    </ul>
  </section>

  <section class="card back" aria-label="Card back">
    <div class="brand">
      <div class="wordmark"><span class="wordmark-square"></span>VEXTORIAL</div>
      <div class="tagline">developer of custom applications</div>
    </div>
    <div class="services">
      <h2 class="services-title">Our Services</h2>
      <ul class="services-list">
        <li>Reduce data-entry errors</li>
        <li>Decrease turnaround times</li>
        <li>Remove bottlenecks in your workflows</li>
        <li>Save time by automating routine processes</li>
        <li>Use reporting tools to make business<br>decisions backed by data</li>
        <li class="service-bitcoin">Bitcoin education: acquire and hold securely</li>
        <li class="service-bitcoin">Bitcoin payments for your existing systems</li>
      </ul>
    </div>
  </section>
</main>
</body>
</html>
```